Business Cards for new orthopaedic surgery practice

My husband and I are starting our own orthopaedic surgery practice. We are looking for a business card that is uniform, but one will have my name/title and the other will have his. You can just create one design with my name on it for now. But when I choose your design as the winning design I will ask that you add another copy with his name/title.

We are looking for classy, simple, elite all in one. We like dark blues/a little gold/yellow. Something that goes with our logo. We want our logo incorporated. Here is all the info you need:
Business name: RV Bone & Vitality Center
Location: 38517 North Willowmere Ave
Coral Springs, FL 33071
Phone: 954-218-4063
Fax: 954-582-7341
Email: info@myrvbonecare.example

Names: Lydia Vance, M.D.
Board Certified Hand and Upper Extremity Surgeon

Ebo Dansu, M.D.
Board Certified Hip & Knee Replacement/General Orthopaedic Surgeon

Can decide what you want to put on the back. Maybe a slogan:
Rooted in Care. Focused on You

I am just going to upload our logo. The only thing is if we select you as the winning design, the location, and phone numbers may change. We will need your help to update that once fully solidified.

Industry/Entity Type

Medical

Contact Information for Business Card

Colors
0054AA
0677BA
7BADD7
CADEEF
E8F1F8
0094D4
00A9DD
6FCCEA
C7EBF8
E9F6FB

Requirements
Must have
• class, appeal,
Should not have
• We want to air on the side of masculine if we are looking at masculine vs. feminine feel. But we still want it classy, sophisticated, and something we will love

```html
<!DOCTYPE html>
<html lang="en">
<head>
<meta charset="utf-8">
<title>RV Bone &amp; Vitality Center – Business Cards</title>
<link href="https://fonts.googleapis.com/css2?family=Montserrat:wght@400;500;700&family=Cinzel:wght@500&display=swap" rel="stylesheet">
<style>
  :root {
    --navy: #1c2a55;
    --navy-deep: #17234a;
    --navy-soft: #26386b;
    --navy-faint: #2a3d74;
    --gold: #c9a24a;
    --white: #ffffff;
    --backdrop: #e6e8ee;
  }
  html, body {
    margin: 0;
    width: 1200px;
    height: 912px;
    overflow: hidden;
    background: var(--backdrop);
  }
  .canvas {
    position: relative;
    width: 1200px;
    height: 912px;
  }
  .card {
    position: absolute;
    left: 280px;
    width: 640px;
    height: 366px;
    overflow: hidden;
    background: var(--navy);
    box-shadow: 0 10px 28px rgba(0,0,0,.25);
  }
  .card--back { top: 70px; background: linear-gradient(120deg, var(--navy-soft), var(--navy) 55%); }
  .card--front { top: 476px; }

  /* back */
  .back-mark {
    position: absolute;
    left: 40px;
    top: 110px;
    width: 330px;
    font-family: "Cinzel", serif;
    font-weight: 500;
    font-size: 40px;
    line-height: 1.15;
    color: var(--navy-faint);
  }
  .back-badge {
    position: absolute;
    right: 40px;
    top: 44px;
    width: 150px;
    height: 150px;
    border-radius: 50%;
    border: 1.5px solid var(--gold);
    display: flex;
    align-items: center;
    justify-content: center;
    text-align: center;
  }
  .back-badge__name {
    font-family: "Cinzel", serif;
    font-weight: 500;
    font-size: 15px;
    line-height: 1.3;
    color: var(--white);
    width: 120px;
  }

  /* front */
  .front-seal {
    position: absolute;
    left: 300px;
    top: -26px;
    width: 360px;
    height: 360px;
    border-radius: 50%;
    background: var(--white);
  }
  .front-seal svg { position: absolute; inset: 0; }
  .front-seal__name {
    position: absolute;
    left: 70px;
    top: 120px;
    width: 220px;
    text-align: center;
    font-family: "Cinzel", serif;
    font-weight: 500;
    font-size: 24px;
    line-height: 1.25;
    color: var(--navy);
  }
  .details {
    position: absolute;
    left: 38px;
    top: 58px;
    font-family: "Montserrat", sans-serif;
    color: var(--white);
  }
  .details__name {
    margin: 0;
    font-weight: 700;
    font-size: 21px;
    letter-spacing: .5px;
    color: var(--gold);
    text-transform: uppercase;
  }
  .details__title {
    margin: 4px 0 0;
    font-size: 13px;
    line-height: 1.3;
  }
  .rule {
    width: 34px;
    height: 3px;
    background: var(--gold);
    margin: 22px 0;
  }
  .details__address { margin: 0; font-size: 13px; line-height: 1.35; }
  .contact { list-style: none; margin: 0; padding: 0; font-size: 13px; line-height: 1.5; }
  .contact li { display: flex; align-items: center; gap: 8px; }
  .contact svg { width: 11px; height: 11px; flex: none; }
  .contact .web-host { color: var(--gold); }
</style>
</head>
<body>
<main class="canvas">

  <section class="card card--back" aria-label="Card back">
    <div class="back-mark">RV Bone &amp; Vitality Center</div>
    <div class="back-badge">
      <span class="back-badge__name">RV Bone &amp; Vitality Center</span>
    </div>
  </section>

  <section class="card card--front" aria-label="Card front">
    <div class="front-seal">
      <svg viewBox="0 0 360 360" aria-hidden="true">
        <path d="M60 230 A130 130 0 0 0 110 285" fill="none" stroke="var(--gold)" stroke-width="3"/>
        <path d="M300 130 A130 130 0 0 0 250 75" fill="none" stroke="var(--gold)" stroke-width="3"/>
      </svg>
      <div class="front-seal__name">RV Bone &amp; Vitality Center</div>
    </div>

    <div class="details">
      <h1 class="details__name">Lydia Vance, M.D</h1>
      <p class="details__title">Board Certified Hand and<br>Upper Extremity Surgeon</p>
      <div class="rule"></div>
      <p class="details__address">38517 North Willowmere Ave<br>Maple Ridge, FL 33984</p>
      <div class="rule"></div>
      <ul class="contact">
        <li><svg viewBox="0 0 12 12"><path d="M3 1 L5 3.5 L4 5 Q5 7 7 8 L8.5 7 L11 9 L9.5 11 Q5 11 2.5 7 Q1 4.5 1.5 2.5 Z" fill="var(--gold)"/></svg><span>954-218-4063</span></li>
        <li><svg viewBox="0 0 12 12"><rect x="1" y="4" width="10" height="6" fill="none" stroke="var(--gold)" stroke-width="1.3"/><rect x="3" y="1" width="6" height="3" fill="none" stroke="var(--gold)" stroke-width="1.3"/></svg><span>954-582-7341</span></li>
        <li><svg viewBox="0 0 12 12"><rect x="1" y="2.5" width="10" height="7" fill="none" stroke="var(--gold)" stroke-width="1.3"/><path d="M1 2.5 L6 7 L11 2.5" fill="none" stroke="var(--gold)" stroke-width="1.3"/></svg><span>info@myrvbonecare.example</span></li>
        <li><svg viewBox="0 0 12 12"><circle cx="6" cy="6" r="5" fill="var(--gold)"/><path d="M1 6 H11 M6 1 V11" stroke="var(--navy)" stroke-width=".8"/></svg><span>www.<span class="web-host">myrvbonecare</span>.example</span></li>
      </ul>
    </div>
  </section>

</main>
</body>
</html>
```